Signage Design Project

Busisness is a bakery and deli long time owned by the Tavel family. Want to develop a new outside sign that communicates it is a deli and a bakery but keeps the tavel name in the design.

The sign when produced will be about 10' by 3' . It is not lighted at present but could be if it were advantageous.

The name of the store is:

Tavel's Harbor Lane Bakery and Deli. The concept is to have a new,modern sign that reinforces that it is a deli and a bakery, as most people only know about the bakery side of the business
Updates

The name Tavel is just a reinforcer so the people kno it is still in the family.  The emphasis should be on the HARBOR LANE BAKERY and DELI

Target Market(s)

Small business breakfast and lunch customers

Industry/Entity Type

Bakery

Requirements
Must have
• Great impact from the road. Communicate that it is a deli and a bakery. Keep the Tavel name but need not be a major design element

```html
<!DOCTYPE html>
<html lang="en">
<head>
<meta charset="utf-8">
<title>Tavel's Harbor Lane Bakery and Deli – Sign</title>
<link rel="stylesheet" href="https://fonts.googleapis.com/css2?family=Kaushan+Script&family=Righteous&display=swap">
<style>
  :root {
    --sign-brown: #a67c52;
    --flourish-brown: #9a714a;
    --letter-gold: #ffc800;
    --shadow-black: #000000;
  }
  html, body {
    margin: 0;
    padding: 0;
    overflow: hidden;
    background: var(--sign-brown);
  }
  .sign {
    position: relative;
    width: 1200px;
    height: 360px;
    background: var(--sign-brown);
    overflow: hidden;
  }
  .flourish {
    position: absolute;
    top: 14px;
    width: 62px;
    height: 332px;
    background: var(--flourish-brown);
    border-radius: 30px;
  }
  .flourish--left { left: 12px; }
  .flourish--right { right: 12px; }
  .family-name {
    position: absolute;
    top: 70px;
    left: 0;
    width: 100%;
    margin: 0;
    text-align: center;
    font-family: "Kaushan Script", cursive;
    font-weight: 400;
    font-size: 70px;
    line-height: 1;
    color: var(--letter-gold);
    text-shadow: -3px 4px 0 var(--shadow-black);
  }
  .trade-name {
    position: absolute;
    top: 178px;
    left: 0;
    width: 100%;
    margin: 0;
    text-align: center;
    font-family: "Righteous", sans-serif;
    font-weight: 400;
    font-size: 132px;
    line-height: 1;
    letter-spacing: 2px;
    color: var(--letter-gold);
    text-shadow: -5px 7px 0 var(--shadow-black);
  }
</style>
</head>
<body>
  <main class="sign">
    <div class="flourish flourish--left" role="img" aria-label="Decorative scroll flourish border, left"></div>
    <div class="flourish flourish--right" role="img" aria-label="Decorative scroll flourish border, right"></div>
    <h2 class="family-name">Tavel's Harbor Lane</h2>
    <h1 class="trade-name">Bakery and Deli</h1>
  </main>
</body>
</html>
```